Web Developer Needs a Business Card Design

I need a personal business card design that represents me as a web developer for potential employers. I would like the background to be a dark color on the front for contrast with my logo and name. The back will have all my information along with a smaller version of the logo. I want something with a modern look and feel, not too conservative. This will be used for potential employers and freelance work.

Industry/Entity Type

Business

Contact Information for Business Card

Front should have my logo and name. The back should have all my personal information which would include: name: Tom Varulek, phone: 570-614-3098, email: tomvarulek@quillbox.net, website url: www.tomvarulek.net, logo, web developer.

Font styles to use
Sans Serif

Requirements
Must have
• Must include my logo. The color palette base color will be the logo color.

```html
<!DOCTYPE html>
<html lang="en">
<head>
<meta charset="utf-8">
<title>Tom Varulek — Business Card</title>
<link rel="stylesheet" href="https://fonts.googleapis.com/css2?family=Questrial&display=swap">
<style>
  :root {
    --backdrop: #3b3b3d;
    --card-dark: #221a18;
    --card-dark-soft: #2e2624;
    --mint: #4fdbbb;
    --mint-deep: #3cc7a6;
    --ink: #1e1816;
    --paper-light: #e9e6e4;
    --muted: #a9a39f;
  }
  * { box-sizing: border-box; margin: 0; padding: 0; }
  html, body { width: 1200px; height: 768px; overflow: hidden; }
  body {
    background: var(--backdrop);
    font-family: "Questrial", "Century Gothic", sans-serif;
    position: relative;
  }
  .card {
    position: absolute;
    top: 232px;
    width: 525px;
    height: 300px;
    border-radius: 3px;
    overflow: hidden;
    box-shadow: 0 10px 28px rgba(0,0,0,.45);
  }
  .card--front { left: 50px; background: var(--card-dark); }
  .card--back { left: 625px; background: var(--card-dark); }

  /* front */
  .front-photo {
    position: absolute; inset: 0;
    background:
      linear-gradient(90deg, #3a3a3c 0%, #2b2626 22%, #231c1a 40%, #221a18 70%, #2f2e30 100%);
  }
  .front-content {
    position: absolute; inset: 0;
    display: flex; flex-direction: column; align-items: center; justify-content: center;
  }
  .brand-mark {
    display: flex; align-items: center; gap: 10px;
    color: var(--mint);
    font-size: 22px;
    margin-bottom: 34px;
  }
  .brand-mark__dot {
    width: 40px; height: 40px; border-radius: 50%;
    border: 5px solid var(--mint);
  }
  .holder-name {
    color: var(--paper-light);
    font-size: 26px;
    letter-spacing: 3px;
    text-transform: uppercase;
  }
  .holder-role {
    color: var(--muted);
    font-size: 13px;
    letter-spacing: 2px;
    margin-top: 8px;
  }

  /* back */
  .back-top {
    position: absolute; left: 0; right: 0; top: 0; height: 168px;
    display: flex; align-items: center; justify-content: center;
  }
  .back-top .brand-mark { margin: 0; font-size: 26px; }
  .back-top .brand-mark__dot { width: 52px; height: 52px; border-width: 6px; }
  .contact-band {
    position: absolute; left: 0; right: 0; bottom: 0; height: 132px;
    background: linear-gradient(180deg, var(--mint) 0%, var(--mint-deep) 100%);
    display: grid;
    grid-template-columns: auto auto;
    column-gap: 34px; row-gap: 8px;
    align-content: center; justify-content: center;
    color: var(--ink);
    font-size: 15px;
  }
  .contact-item { display: flex; align-items: center; gap: 7px; white-space: nowrap; }
  .contact-item--phone { grid-column: 1 / span 2; justify-self: center; }
  .contact-icon { width: 16px; height: 16px; flex: none; }
</style>
</head>
<body>

<section class="card card--front" aria-label="Card front">
  <div class="front-photo" role="img" aria-label="Dark desk scene with laptop and keyboard"></div>
  <div class="front-content">
    <div class="brand-mark"><span class="brand-mark__dot"></span><span>Tom Varulek</span></div>
    <h1 class="holder-name">Tom Varulek</h1>
    <p class="holder-role">Front-End Developer</p>
  </div>
</section>

<section class="card card--back" aria-label="Card back">
  <div class="back-top">
    <div class="brand-mark"><span class="brand-mark__dot"></span><span>Tom Varulek</span></div>
  </div>
  <div class="contact-band">
    <div class="contact-item contact-item--phone">
      <svg class="contact-icon" viewBox="0 0 16 16"><circle cx="8" cy="8" r="8" fill="#1e1816"/><path d="M5.2 4.2l1.5-.3.8 2-1 .7a5 5 0 0 0 2.6 2.6l.7-1 2 .8-.3 1.5c-3.6.2-6.5-2.7-6.3-6.3z" fill="#4fdbbb"/></svg>
      <span>570-614-3098</span>
    </div>
    <div class="contact-item">
      <svg class="contact-icon" viewBox="0 0 16 16"><circle cx="8" cy="8" r="8" fill="#1e1816"/><circle cx="8" cy="8" r="4.5" fill="none" stroke="#4fdbbb" stroke-width="1"/><path d="M3.5 8h9M8 3.5c-2 2.5-2 6.5 0 9M8 3.5c2 2.5 2 6.5 0 9" fill="none" stroke="#4fdbbb" stroke-width="1"/></svg>
      <span>www.tomvarulek.net</span>
    </div>
    <div class="contact-item">
      <svg class="contact-icon" viewBox="0 0 16 16"><circle cx="8" cy="8" r="8" fill="#1e1816"/><rect x="4" y="5" width="8" height="6" fill="none" stroke="#4fdbbb" stroke-width="1"/><path d="M4 5l4 3.2L12 5" fill="none" stroke="#4fdbbb" stroke-width="1"/></svg>
      <span>tomvarulek@quillbox.net</span>
    </div>
    <div class="contact-item">
      <svg class="contact-icon" viewBox="0 0 16 16"><circle cx="8" cy="8" r="8" fill="#1e1816"/></svg>
      <span>tomvarulek.net</span>
    </div>
    <div class="contact-item">
      <svg class="contact-icon" viewBox="0 0 16 16"><circle cx="8" cy="8" r="8" fill="#1e1816"/></svg>
      <span>@tomvarulek.net</span>
    </div>
    <div class="contact-item">
      <svg class="contact-icon" viewBox="0 0 16 16"><circle cx="8" cy="8" r="8" fill="#1e1816"/></svg>
      <span>tomvarulek.net</span>
    </div>
  </div>
</section>

</body>
</html>
```